Meridale Bed Company Needs Business Card

Looking for a very nice looking business card. Creative but not extravagant. We sell beds and pillows across the U.S. and need something professional but catchy. I have attached the logo.

Name : Devin Holt
Title : President
Phone : (800) 471-2960
Email: sleep@quilmora.com
Website: www.quilmora.com

Can be single-sided or double-sided
horizontal or vertical

Can use Blues/Greys

Target Market(s)

Mass Market

Industry/Entity Type

Retail

Contact Information for Business Card

Name : Devin Holt
Title : President
Phone : (800) 471-2960
Email: sleep@quilmora.com
Website: www.quilmora.com

Requirements
Must have
• Clean, Modern, Smooth
• Can use Blues/Greys
• On the other side without the information - have something simple like www.quilmora.com or our logo
Nice to have
• Surprise me
Should not have
• Nothing crazy, nothing cluttered

```html
<!DOCTYPE html>
<html lang="en">
<head>
<meta charset="utf-8">
<title>Meridale Bed Company – Business Card</title>
<link href="https://fonts.googleapis.com/css2?family=Nunito+Sans:wght@300;400;700&display=swap" rel="stylesheet">
<style>
  :root {
    --backdrop: #434346;
    --card: #262626;
    --accent: #34a3d4;
    --ink: #ffffff;
  }
  * { box-sizing: border-box; margin: 0; padding: 0; }
  html, body {
    width: 1200px; height: 1200px; overflow: hidden;
    background: var(--backdrop);
    font-family: "Nunito Sans", "Helvetica Neue", Arial, sans-serif;
  }
  .card {
    position: absolute;
    width: 776px; height: 430px;
    background: var(--card);
    box-shadow: 0 14px 18px -10px rgba(0,0,0,0.55);
  }
  .card--front { left: 212px; top: 113px; }
  .card--back { left: 215px; top: 654px; }

  .accent-band {
    position: absolute; right: 0; top: 0;
    width: 167px; height: 100%;
    background: var(--accent);
  }
  .identity { position: absolute; left: 44px; top: 42px; color: var(--ink); }
  .identity__name { font-size: 34px; font-weight: 300; line-height: 1.1; letter-spacing: 0.2px; }
  .identity__name strong { font-weight: 700; }
  .identity__title {
    margin-left: 40px; margin-top: 4px;
    font-size: 19px; font-weight: 400; letter-spacing: 0.6px;
  }
  .contact { position: absolute; left: 62px; top: 180px; list-style: none; }
  .contact__item {
    display: flex; align-items: center;
    height: 40px; margin-bottom: 35px;
    color: var(--ink); font-size: 20px; font-weight: 400;
  }
  .contact__icon { width: 34px; height: 34px; margin-right: 22px; fill: var(--accent); }

  .brand-name {
    position: absolute; left: 0; right: 0; top: 168px;
    text-align: center;
    color: var(--accent);
    font-size: 72px; font-weight: 300; letter-spacing: 2px;
    line-height: 1;
  }
</style>
</head>
<body>
  <section class="card card--front">
    <div class="identity">
      <h1 class="identity__name">Devin <strong>Holt</strong></h1>
      <p class="identity__title">PRESIDENT</p>
    </div>
    <ul class="contact">
      <li class="contact__item">
        <svg class="contact__icon" viewBox="0 0 24 24" aria-hidden="true"><path d="M6.6 10.8c1.4 2.8 3.8 5.1 6.6 6.6l2.2-2.2c.3-.3.7-.4 1-.2 1.1.4 2.3.6 3.6.6.6 0 1 .4 1 1V20c0 .6-.4 1-1 1C10.6 21 3 13.4 3 4c0-.6.4-1 1-1h3.5c.6 0 1 .4 1 1 0 1.3.2 2.5.6 3.6.1.3 0 .7-.2 1z"/></svg>
        (800) 471-2960
      </li>
      <li class="contact__item">
        <svg class="contact__icon" viewBox="0 0 24 24" aria-hidden="true"><path d="M2 5h20v14H2z"/><path d="M2 5l10 8 10-8v1.6l-10 8-10-8z" fill="#262626"/></svg>
        Sleep@quilmora.com
      </li>
      <li class="contact__item">
        <svg class="contact__icon" viewBox="0 0 24 24" aria-hidden="true"><g fill="none" stroke="#34a3d4" stroke-width="1.6"><circle cx="12" cy="12" r="9.5"/><ellipse cx="12" cy="12" rx="4.2" ry="9.5"/><path d="M12 2.5v19M2.5 12h19M4 7h16M4 17h16"/></g></svg>
        www.quilmora.com
      </li>
    </ul>
    <div class="accent-band"></div>
  </section>

  <section class="card card--back">
    <p class="brand-name">quilmora</p>
  </section>
</body>
</html>
```